Design the Business card for NetVaultic

Business card required for a professional Cyber Security business.
Company Logo and Icon has already been provided however I would like other options for the logo and icon to compare to. Alternatively, please refine/enhance the image of the logo.icon I have already provided.

If you are going to use the provided logo and icon, I was thinking that the company raised Logo on White background would serve well on the front of the card. See attached. AND, a large company raised stand-alone icon to appear on black background on the back of the card with tagline 'Cyber Risk Management, Governance and Consulting' or 'Cyber Security for your Business' See attached.
Alternatively, provide your own design for the logo and icon.

Target Market(s)

Enterprise, Government, Financial.

Contact Information for Business Card

Tavin Orloweth
Founder and CEO

Email Address
Mobile Number
Website URL
LinkedIn URL

Logo Text

NetVaultic - see attached example of logo

Font styles to use
Other font styles liked:
• Berlin Sans FB

Requirements
Must have
• Clean large and bold icon on the back with tagline.
• Horizontal alignment,
Nice to have
• Round edges.
• Raised Logo/Icon
Should not have
• An unprofessional look and feel.

```html
<!DOCTYPE html>
<html lang="en">
<head>
<meta charset="utf-8">
<title>NetVaultic Business Card</title>
<link rel="stylesheet" href="https://fonts.googleapis.com/css2?family=Roboto+Condensed:wght@700&family=Roboto:wght@400;500&family=Ubuntu:wght@500&display=swap">
<style>
  :root {
    --backdrop: #262626;
    --card-front: #4673c4;
    --card-back: #1b1c1e;
    --accent-yellow: #f5bd1b;
    --brand-blue: #1b74c4;
    --tagline-blue: #4d72c2;
    --text-light: #ffffff;
    --rivet: #f2f4f8;
  }
  * { margin: 0; padding: 0; box-sizing: border-box; }
  html, body { width: 1200px; height: 960px; overflow: hidden; }
  body { background: var(--backdrop); position: relative; }

  .card {
    position: absolute;
    width: 599px;
    height: 342px;
    border-radius: 18px;
  }
  .card--front { left: 322px; top: 108px; background: var(--card-front); }
  .card--back { left: 321px; top: 494px; background: var(--card-back); }

  .rivet {
    position: absolute;
    width: 11px; height: 11px;
    border-radius: 50%;
    background: var(--rivet);
  }
  .rivet--tl { left: 21px; top: 16px; }
  .rivet--tr { right: 20px; top: 16px; }
  .rivet--bl { left: 21px; bottom: 16px; }
  .rivet--br { right: 20px; bottom: 16px; }

  .identity {
    position: absolute;
    right: 321px;
    top: 150px;
    text-align: right;
  }
  .identity__name {
    font-family: "Roboto Condensed", sans-serif;
    font-weight: 700;
    font-size: 20px;
    color: var(--accent-yellow);
    line-height: 24px;
    letter-spacing: 0.2px;
  }
  .identity__title {
    font-family: "Roboto", sans-serif;
    font-weight: 500;
    font-size: 14px;
    color: var(--text-light);
    line-height: 20px;
  }

  .divider {
    position: absolute;
    left: 297px;
    top: 129px;
    width: 1px;
    height: 85px;
    background: rgba(255,255,255,0.75);
  }

  .contacts {
    position: absolute;
    left: 315px;
    top: 132px;
    list-style: none;
  }
  .contacts__item {
    display: flex;
    align-items: center;
    height: 19px;
    font-family: "Roboto", sans-serif;
    font-size: 14px;
    color: var(--text-light);
  }
  .contacts__icon {
    width: 13px; height: 13px;
    margin-right: 10px;
    flex: none;
  }

  .brand {
    position: absolute;
    left: 123px;
    top: 116px;
    display: flex;
    align-items: center;
  }
  .brand__dot {
    width: 70px; height: 70px;
    border-radius: 50%;
    background: var(--brand-blue);
    margin-right: 24px;
  }
  .brand__name {
    font-family: "Ubuntu", sans-serif;
    font-weight: 500;
    font-size: 46px;
    color: var(--brand-blue);
  }

  .tagline {
    position: absolute;
    left: 0; right: 0;
    top: 276px;
    text-align: center;
    font-family: "Ubuntu", sans-serif;
    font-weight: 500;
    font-size: 17px;
    color: var(--tagline-blue);
  }
  .tagline__accent { color: var(--accent-yellow); }
</style>
</head>
<body>
  <section class="card card--front" aria-label="Card front">
    <span class="rivet rivet--tl"></span>
    <span class="rivet rivet--tr"></span>
    <span class="rivet rivet--bl"></span>
    <span class="rivet rivet--br"></span>

    <div class="identity">
      <p class="identity__name">TAVIN ORLOWETH</p>
      <p class="identity__title">FOUNDER &amp; CEO</p>
    </div>

    <span class="divider"></span>

    <ul class="contacts">
      <li class="contacts__item">
        <svg class="contacts__icon" viewBox="0 0 13 13" aria-hidden="true">
          <rect x="3" y="0.5" width="7" height="12" rx="1.2" fill="none" stroke="#f5bd1b" stroke-width="1.4"/>
          <rect x="5" y="10" width="3" height="1" fill="#f5bd1b"/>
        </svg>555 014 2290
      </li>
      <li class="contacts__item">
        <svg class="contacts__icon" viewBox="0 0 13 13" aria-hidden="true">
          <rect x="0.5" y="3" width="12" height="8" fill="#f5bd1b"/>
          <path d="M0.5 3 L6.5 7.5 L12.5 3" fill="none" stroke="#4673c4" stroke-width="1"/>
        </svg>tavin@netvaultic.com
      </li>
      <li class="contacts__item">
        <svg class="contacts__icon" viewBox="0 0 13 13" aria-hidden="true">
          <circle cx="6.5" cy="6.5" r="6" fill="#f5bd1b"/>
          <ellipse cx="6.5" cy="6.5" rx="2.5" ry="6" fill="none" stroke="#4673c4" stroke-width="0.9"/>
          <line x1="0.5" y1="6.5" x2="12.5" y2="6.5" stroke="#4673c4" stroke-width="0.9"/>
        </svg>www.netvaultic.com
      </li>
      <li class="contacts__item">
        <svg class="contacts__icon" viewBox="0 0 13 13" aria-hidden="true">
          <circle cx="6.5" cy="6.5" r="6" fill="#f5bd1b"/>
        </svg>netvaultic
      </li>
    </ul>
  </section>

  <section class="card card--back" aria-label="Card back">
    <div class="brand">
      <span class="brand__dot"></span>
      <span class="brand__name">NetVaultic</span>
    </div>
    <p class="tagline">Cyber Risk Management, <span class="tagline__accent">Governance &amp; Consulting</span></p>
  </section>
</body>
</html>
```